eBook-Cover für Thriller gesucht
An dieser Stelle ein großes Lob und vielen Dank an die Designerin Larosa. Auch das zweite Buchcover ist wieder überaus gelungen, eine ganz tolle Arbeit. Auch die angenehme Zusammenarbeit war mir, wie schon beim ersten Auftrag, eine Freude. Ebenso hervorzuheben ist die Schnelligkeit und Kreativität, mit der die Designerin auf Änderungswünsche reagiert. Als Auftraggeber gebe ich verdiente fünf Sterne und bin mit dem Ergebnis wirklich sehr zufrieden.
Zielgruppe
Ich bin Autor. Zielgruppe sind (anspruchsvolle) Leser/innen von Thrillern und Kriminalromanen im ebook-Bereich.
Aufgabenstellung
- Gesucht wird ein ebook-Cover für einen Thriller mit dem Titel 'Kaltgrund'
- Grobe Aufteilung siehe Skizzen
- Fokus des Covers liegt auf dem Buchtitel und dem Motiv ('Blauer Drachen')
- Hintergrund eher hell, Assoziation mit zarter Eisfläche mit angedeuteten Rissen vom Hauptmotiv ausgehend. Dadurch auch Tiefe und Dreidimensionalität. (Beispiel zum Hintergrund: 'Schattenfrist' von Heinrich Wendel, jedoch ohne Blut )
-Titelschrift groß, Stil 'gekratzt' bzw. 'gestrichelt', (Schriftart ähnlich wie Autorenname bei 'Die Schleuse' von Matthias Kolbe). Schrift groß und 'treppenförmig' neben dem Hauptmotiv angeordnet. Schriftfarbe schwarz/dunkelblau, ähnlich Hauptmotiv (Bsp.: 'Schwarzeid' von Heinrich Wendel)
Hauptmotiv ist der vom rechten Coverrand hineinragende 'Blaue Drachen' (Glaucus atlanticus, siehe hochgeladenes Beispielbild von Wissnetz)
- Schriftart von Autorenname und Genre eher klar
- eigene Detailvorschläge zur Optimierung des Ergebnisses möglich bzw. erwünscht

```html
<!DOCTYPE html>
<html lang="de">
<head>
<meta charset="utf-8">
<title>Kaltgrund – Lorenz Halbach</title>
<link rel="stylesheet" href="https://fonts.googleapis.com/css2?family=Cinzel:wght@400;700&family=Cabin+Sketch:wght@700&display=swap">
<style>
  :root {
    --ice-light: #e4ecee;
    --ice-frost: #f4f7f7;
    --ice-mid: #bccfd3;
    --ice-deep: #9ab6bc;
    --ice-shadow: #8ea6ac;
    --ice-glow: #f1dcd2;
    --ink-navy: #15203a;
    --title-glass: #4b9aa6;
    --frost-white: #ffffff;
    --dragon-deep: #1c2a72;
    --dragon-mid: #34509e;
    --dragon-light: #a9b9d6;
  }
  html, body {
    margin: 0;
    padding: 0;
    width: 724px;
    height: 1200px;
    overflow: hidden;
    background: var(--ice-light);
  }
  .cover {
    position: relative;
    width: 724px;
    height: 1200px;
    overflow: hidden;
  }
  .ice-surface {
    position: absolute;
    inset: 0;
    background:
      radial-gradient(ellipse 170px 110px at 210px 200px, var(--ice-glow) 0%, rgba(241,220,210,0) 100%),
      radial-gradient(ellipse 120px 70px at 420px 220px, rgba(241,220,210,0.7) 0%, rgba(241,220,210,0) 100%),
      radial-gradient(ellipse 160px 260px at 90px 520px, rgba(244,247,247,0.8) 0%, rgba(244,247,247,0) 100%),
      radial-gradient(ellipse 140px 200px at 330px 980px, rgba(244,247,247,0.55) 0%, rgba(244,247,247,0) 100%),
      radial-gradient(ellipse 120px 260px at 60px 1080px, rgba(244,247,247,0.6) 0%, rgba(244,247,247,0) 100%),
      radial-gradient(ellipse 200px 120px at 610px 100px, rgba(142,166,172,0.55) 0%, rgba(142,166,172,0) 100%),
      radial-gradient(ellipse 180px 240px at 600px 760px, rgba(142,166,172,0.45) 0%, rgba(142,166,172,0) 100%),
      radial-gradient(ellipse 200px 160px at 560px 1130px, rgba(142,166,172,0.5) 0%, rgba(142,166,172,0) 100%),
      linear-gradient(175deg, var(--ice-light) 0%, var(--ice-mid) 55%, var(--ice-deep) 100%);
  }
  .ice-lines {
    position: absolute;
    inset: 0;
  }
  .blue-dragon {
    position: absolute;
    inset: 0;
  }
  .author {
    position: absolute;
    top: 40px;
    left: 0;
    width: 724px;
    margin: 0;
    text-align: center;
    font-family: "Cinzel", serif;
    font-weight: 400;
    font-size: 62px;
    letter-spacing: 1px;
    color: var(--ink-navy);
  }
  .title {
    margin: 0;
    font-family: "Cabin Sketch", cursive;
    font-weight: 700;
    color: var(--title-glass);
    text-shadow: 0 0 3px var(--frost-white), 0 0 8px var(--frost-white), 0 0 16px rgba(255,255,255,0.85);
  }
  .title-step {
    position: absolute;
    display: block;
    font-size: 240px;
    line-height: 1;
    letter-spacing: 2px;
    transform: scaleX(0.8);
    transform-origin: left top;
    white-space: nowrap;
  }
  .title-step--one   { left: 22px;  top: 309px; }
  .title-step--two   { left: 150px; top: 605px; }
  .title-step--three { left: 285px; top: 809px; }
  .genre {
    position: absolute;
    top: 1136px;
    left: 0;
    width: 724px;
    margin: 0;
    text-align: center;
    font-family: "Cinzel", serif;
    font-weight: 700;
    font-size: 40px;
    letter-spacing: 15px;
    text-indent: 15px;
    color: var(--ink-navy);
  }
</style>
</head>
<body>
  <main class="cover">
    <div class="ice-surface"></div>
    <svg class="ice-lines" width="724" height="1200" viewBox="0 0 724 1200" aria-hidden="true">
      <g fill="none" stroke="#ffffff" stroke-linecap="round" opacity="0.55">
        <path d="M0 990 L250 720" stroke-width="2"/>
        <path d="M40 1200 L300 880" stroke-width="1.2"/>
        <path d="M510 560 L455 1200" stroke-width="2"/>
        <path d="M610 600 L665 1060" stroke-width="1.5"/>
        <path d="M700 500 L640 1200" stroke-width="1"/>
        <path d="M0 300 L180 120" stroke-width="1"/>
        <path d="M0 640 L120 560" stroke-width="1"/>
      </g>
      <g fill="none" stroke="#55666c" stroke-width="1" stroke-linecap="round" opacity="0.75">
        <path d="M320 140 L380 200 L425 255"/>
        <path d="M380 200 L362 240 L356 282"/>
        <path d="M380 200 L438 172 L470 138"/>
        <path d="M250 248 L330 262 L425 255"/>
      </g>
    </svg>
    <svg class="blue-dragon" width="724" height="1200" viewBox="0 0 724 1200" role="img" aria-label="Blauer Drache (Glaucus atlanticus), vom rechten Rand ins Eis ragend">
      <defs>
        <radialGradient id="dragon-tone" cx="0.55" cy="0.5" r="0.5">
          <stop offset="0" stop-color="var(--dragon-light)"/>
          <stop offset="0.35" stop-color="var(--dragon-mid)"/>
          <stop offset="0.75" stop-color="var(--dragon-deep)" stop-opacity="0.75"/>
          <stop offset="1" stop-color="var(--dragon-deep)" stop-opacity="0"/>
        </radialGradient>
      </defs>
      <ellipse cx="560" cy="400" rx="300" ry="200" transform="rotate(28 560 400)" fill="url(#dragon-tone)"/>
    </svg>
    <p class="author">LORENZ HALBACH</p>
    <h1 class="title" aria-label="Kaltgrund">
      <span class="title-step title-step--one">KAL</span>
      <span class="title-step title-step--two">TGR</span>
      <span class="title-step title-step--three">UND</span>
    </h1>
    <p class="genre">THRILLER</p>
  </main>
</body>
</html>
```